Business card for a Exhibition booth fabrication company

Hi. My company would like to change our corporate name card. We are an events and Exhibition stand builder company. We would like our corporate name card to resonate what we do. I need someone to create something unique that relates to the industry that I am in. The graphic designer should be creative to incorporate the elements of my industry and try to blend in well in the design of the card. Our aim is to ensure that we are unique and our card can look different from our competitors.
Updates

Target Market(s)

Marketing and events manager from all companies

Contact Information for Business Card

The business card should have the following details:
Name
Job Title
Email
Website

Colors

Designer to choose colors to be used in the design.

Requirements
Must have
• The card must be look something that is relevant to the service that I am providing. My website is: www.velmora-buildworks.com
• You can see my website to get more information on what service that I am doing
Nice to have
• On the back of my card, I would like to have a globe image with the incorporation of my company logo. This is to indicate that my services can be done in any part of the world.

```html
<!DOCTYPE html>
<html lang="en">
<head>
<meta charset="utf-8">
<title>Velmora Buildworks – Business Card</title>
<link href="https://fonts.googleapis.com/css2?family=Montserrat:wght@500;700&family=PT+Serif:wght@400&display=swap" rel="stylesheet">
<style>
  :root {
    --backdrop: #8f8f8f;
    --card: #ffffff;
    --brand-red: #e31e26;
    --ink: #2b2b2b;
    --charcoal: #2a2a2a;
    --globe-light: #f1f1f1;
    --globe-mid: #e2e2e2;
    --globe-dark: #d2d2d2;
  }
  * { box-sizing: border-box; margin: 0; padding: 0; }
  html, body { width: 1200px; height: 1200px; overflow: hidden; }
  body {
    background: var(--backdrop);
    display: flex;
    flex-direction: column;
    align-items: center;
    justify-content: center;
    gap: 70px;
  }
  .card {
    position: relative;
    width: 840px;
    height: 480px;
    background: var(--card);
    overflow: hidden;
    box-shadow: 0 10px 28px rgba(0,0,0,.25);
  }
  .globe-area {
    position: absolute;
    border-radius: 50% 50% 46% 46% / 60% 60% 40% 40%;
    background: linear-gradient(160deg, var(--globe-light) 0%, var(--globe-mid) 45%, var(--globe-dark) 100%);
    opacity: .85;
  }
  .brand {
    position: absolute;
    display: flex;
    align-items: center;
    gap: 14px;
    font-family: "Montserrat", sans-serif;
    font-weight: 700;
    color: var(--ink);
    letter-spacing: .12em;
    text-transform: uppercase;
    white-space: nowrap;
  }
  .brand-dot { border-radius: 50%; background: var(--brand-red); flex: none; }

  /* front */
  .card-front .globe-area { left: 150px; top: 60px; width: 600px; height: 300px; }
  .card-front .brand { left: 48px; top: 54px; font-size: 22px; }
  .card-front .brand-dot { width: 22px; height: 22px; }
  .person { position: absolute; left: 300px; top: 150px; }
  .person-name {
    font-family: "Montserrat", sans-serif;
    font-weight: 700;
    font-size: 46px;
    line-height: 1.1;
    color: var(--brand-red);
    letter-spacing: .02em;
    text-transform: uppercase;
  }
  .person-title {
    font-family: "PT Serif", serif;
    font-size: 26px;
    color: var(--ink);
    padding-bottom: 8px;
    border-bottom: 2px solid var(--brand-red);
    width: 150px;
  }
  .contacts {
    position: absolute; left: 110px; top: 300px;
    font-family: "PT Serif", serif;
    font-size: 19px;
    color: var(--ink);
    list-style: none;
  }
  .contacts li { display: flex; align-items: center; gap: 12px; margin-bottom: 6px; }
  .contacts svg { width: 20px; height: 20px; flex: none; }
  .address {
    position: absolute; left: 60px; top: 374px;
    font-family: "PT Serif", serif; font-size: 16px; color: var(--ink); line-height: 1.35;
  }
  .edge-band { position: absolute; left: 0; right: 0; bottom: 0; height: 46px; display: flex; }
  .edge-band .dark { width: 200px; background: var(--charcoal); }
  .edge-band .red { flex: 1; background: var(--brand-red); border-top-left-radius: 18px; margin-left: -10px; }

  /* back */
  .card-back .globe-area { left: 150px; top: 70px; width: 620px; height: 340px; }
  .card-back .brand {
    left: 0; right: 0; top: 0; bottom: 0; justify-content: center;
    font-size: 34px;
  }
  .card-back .brand-dot { width: 32px; height: 32px; }
</style>
</head>
<body>
  <section class="card card-front">
    <div class="globe-area" role="img" aria-label="Light grey world map showing the continents, signalling stands built worldwide"></div>
    <div class="brand"><span class="brand-dot"></span>Velmora Buildworks</div>
    <div class="person">
      <h1 class="person-name">Darel Voss</h1>
      <p class="person-title">Director</p>
    </div>
    <ul class="contacts">
      <li>
        <svg viewBox="0 0 20 20"><rect x="1" y="4" width="18" height="12" rx="1.5" fill="var(--brand-red)"/><path d="M2 5l8 6 8-6" stroke="#fff" stroke-width="1.6" fill="none"/></svg>
        username@velmora-buildworks.com
      </li>
      <li>
        <svg viewBox="0 0 20 20"><circle cx="10" cy="10" r="9" fill="var(--brand-red)"/><g stroke="#fff" stroke-width="1.2" fill="none"><ellipse cx="10" cy="10" rx="4" ry="9"/><path d="M1 10h18M3 5.5h14M3 14.5h14"/></g></svg>
        www.velmora-buildworks.com
      </li>
    </ul>
    <p class="address">4812 Harbor Lane 300<br>Austin, TX 73301</p>
    <div class="edge-band"><span class="dark"></span><span class="red"></span></div>
  </section>

  <section class="card card-back">
    <div class="globe-area" role="img" aria-label="Light grey world map behind the company name, showing global reach"></div>
    <div class="brand"><span class="brand-dot"></span>Velmora Buildworks</div>
  </section>
</body>
</html>
```